Software Development Consulting Company Needs Business Card Design

We need a new business card design for our consultants at Kestrel Works (kestrelworks.example). We are a small firm that provides high-end software development and methodology consulting to medium to large enterprise IT organizations.

Our logo uses Futura for the font and we would like to stick with navy blue and canary yellow for the logo colors. Attached are normal and reversed versions of our logos in illustrator format.
Updates

Hi Everyone, Thank yo very much for your amazing design ideas. I have created a poll for this project and our employees will be voting on the design they wish to use. We will be making a decision this Wednesday (October 22nd). Thanks again, Dale Hartwick

Industry/Entity Type

Business

```html
<!DOCTYPE html>
<html lang="en">
<head>
<meta charset="utf-8">
<title>Kestrel Works – Business Card</title>
<link href="https://fonts.googleapis.com/css2?family=Jost:wght@400;500&family=Open+Sans:wght@400;700&display=swap" rel="stylesheet">
<style>
  :root {
    --navy: #1f4670;
    --navy-ink: #1c3f66;
    --canary: #e6e619;
    --paper: #ffffff;
    --ground: #ecebe8;
    --rule: #c9ccd2;
    --text: #2c3440;
    --muted: #5a6270;
  }
  * { box-sizing: border-box; margin: 0; padding: 0; }
  html, body { width: 1200px; height: 720px; overflow: hidden; }
  body {
    background: var(--ground);
    display: flex;
    align-items: center;
    justify-content: center;
    gap: 40px;
  }
  .card {
    width: 540px;
    height: 309px;
    position: relative;
    box-shadow: 0 2px 10px rgba(0,0,0,.12);
  }
  .card--front { background: var(--paper); }
  .card--back { background: var(--navy); color: var(--paper); }

  .wordmark {
    display: flex;
    align-items: center;
    gap: 12px;
    font-family: "Jost", "Futura", sans-serif;
    font-weight: 500;
    letter-spacing: .16em;
    text-transform: uppercase;
    white-space: nowrap;
  }
  .wordmark__dot {
    width: 12px; height: 12px;
    border-radius: 50%;
    background: var(--canary);
    flex: none;
  }

  .card--front .wordmark {
    position: absolute;
    left: 30px; top: 137px;
    font-size: 24px;
    color: var(--navy-ink);
  }
  .divider {
    position: absolute;
    left: 300px; top: 36px;
    width: 1px; height: 130px;
    background: var(--rule);
  }
  .contact {
    position: absolute;
    left: 318px; top: 40px;
    font-family: "Open Sans", sans-serif;
    color: var(--text);
  }
  .contact__name {
    font-weight: 700;
    font-size: 17px;
    color: var(--navy-ink);
    line-height: 1.1;
  }
  .contact__title {
    font-size: 11px;
    color: var(--muted);
    margin-bottom: 10px;
  }
  .contact__list { list-style: none; }
  .contact__item {
    display: flex;
    align-items: center;
    gap: 7px;
    font-size: 11.5px;
    line-height: 22px;
  }
  .contact__icon { width: 12px; height: 12px; fill: var(--navy-ink); flex: none; }

  .card--back .wordmark {
    position: absolute;
    left: 50%; top: 108px;
    transform: translateX(-50%);
    font-size: 32px;
    color: var(--paper);
  }
  .card--back .web {
    position: absolute;
    left: 0; right: 0; top: 206px;
    text-align: center;
    font-family: "Open Sans", sans-serif;
    font-size: 16px;
    letter-spacing: .14em;
  }
</style>
</head>
<body>
  <section class="card card--front" aria-label="Business card front">
    <div class="wordmark"><span class="wordmark__dot"></span><span>Kestrel Works</span></div>
    <div class="divider"></div>
    <div class="contact">
      <p class="contact__name">Your Name</p>
      <p class="contact__title">Title</p>
      <ul class="contact__list">
        <li class="contact__item">
          <svg class="contact__icon" viewBox="0 0 24 24" aria-hidden="true"><path d="M6.6 10.8a15.1 15.1 0 0 0 6.6 6.6l2.2-2.2a1 1 0 0 1 1-.25 11.4 11.4 0 0 0 3.6.57 1 1 0 0 1 1 1V20a1 1 0 0 1-1 1A17 17 0 0 1 3 4a1 1 0 0 1 1-1h3.5a1 1 0 0 1 1 1c0 1.25.2 2.45.57 3.57a1 1 0 0 1-.25 1z"/></svg>
          012-345-6789
        </li>
        <li class="contact__item">
          <svg class="contact__icon" viewBox="0 0 24 24" aria-hidden="true"><path d="M2 5h20v14H2zm2 2v.5l8 5 8-5V7z"/></svg>
          info@kestrelworks.example
        </li>
        <li class="contact__item">
          <svg class="contact__icon" viewBox="0 0 24 24" aria-hidden="true"><path d="M12 2a10 10 0 1 0 0 20 10 10 0 0 0 0-20zm0 2c.9 0 2.1 1.9 2.6 5H9.4C9.9 5.9 11.1 4 12 4zM4.3 11h3c0 .7 0 1.4.1 2h-3a8 8 0 0 1-.1-2zm5.1 2a18 18 0 0 1 0-2h5.2a18 18 0 0 1 0 2zm7.2 0c.1-.6.1-1.3.1-2h3a8 8 0 0 1 0 2zM12 20c-.9 0-2.1-1.9-2.6-5h5.2c-.5 3.1-1.7 5-2.6 5z"/></svg>
          www.kestrelworks.example
        </li>
        <li class="contact__item">
          <svg class="contact__icon" viewBox="0 0 24 24" aria-hidden="true"><path d="M12 2a7 7 0 0 0-7 7c0 5.2 7 13 7 13s7-7.8 7-13a7 7 0 0 0-7-7zm0 9.5A2.5 2.5 0 1 1 12 6.5a2.5 2.5 0 0 1 0 5z"/></svg>
          Riverton + Oakdale, IL
        </li>
      </ul>
    </div>
  </section>

  <section class="card card--back" aria-label="Business card back">
    <div class="wordmark"><span class="wordmark__dot"></span><span>Kestrel Works</span></div>
    <p class="web">www.kestrelworks.example</p>
  </section>
</body>
</html>
```